Business card design for my company.
I would like the card's background colour to be black. You can also see our web site to get an idea of our brand. https://www.tmwhomecrafting.com.au/
- Name
- Email

```html
<!DOCTYPE html>
<html lang="en">
<head>
<meta charset="utf-8">
<title>TMW Home Crafting – Business Card</title>
<link href="https://fonts.googleapis.com/css2?family=Montserrat:wght@400;500;700&display=swap" rel="stylesheet">
<style>
  :root {
    --stage: #2c2c2c;
    --card: #151515;
    --green: #1f9a4a;
    --white: #f2f2f2;
    --emboss: #3a3a3a;
  }
  html, body {
    margin: 0;
    padding: 0;
    width: 1200px;
    height: 694px;
    overflow: hidden;
    background: var(--stage);
    font-family: "Montserrat", Arial, sans-serif;
  }
  .stage {
    position: relative;
    width: 1200px;
    height: 694px;
    display: flex;
    align-items: center;
    justify-content: center;
    gap: 40px;
  }
  .card {
    position: relative;
    width: 540px;
    height: 309px;
    background: var(--card);
    border-radius: 18px;
    overflow: hidden;
  }

  /* Front */
  .card-front {
    display: flex;
    align-items: center;
    justify-content: center;
  }
  .front-name {
    display: flex;
    align-items: center;
    gap: 14px;
    font-weight: 700;
    font-size: 30px;
    letter-spacing: 3px;
    text-transform: uppercase;
    color: var(--emboss);
  }
  .front-name .mark-square {
    width: 26px;
    height: 26px;
    background: var(--emboss);
  }

  /* Back */
  .brand-name {
    position: absolute;
    top: 38px;
    right: 34px;
    display: flex;
    align-items: center;
    gap: 10px;
    font-weight: 700;
    font-size: 20px;
    letter-spacing: 1.5px;
    text-transform: uppercase;
    color: var(--white);
  }
  .brand-name .mark-square {
    width: 16px;
    height: 16px;
    background: var(--white);
  }
  .person {
    position: absolute;
    left: 34px;
    top: 118px;
  }
  .person-name {
    margin: 0;
    font-weight: 700;
    font-size: 30px;
    color: var(--green);
    line-height: 1.1;
  }
  .person-title {
    margin: 4px 0 0;
    font-weight: 400;
    font-size: 15px;
    color: var(--white);
  }
  .divider {
    position: absolute;
    left: 34px;
    right: 34px;
    top: 188px;
    height: 2px;
    background: var(--green);
  }
  .contacts {
    position: absolute;
    left: 34px;
    top: 206px;
    margin: 0;
    padding: 0;
    list-style: none;
  }
  .contact,
  .address {
    display: flex;
    align-items: center;
    gap: 10px;
    font-size: 13px;
    color: var(--white);
    margin-bottom: 8px;
  }
  .address {
    position: absolute;
    right: 34px;
    top: 206px;
    margin: 0;
  }
  .icon {
    width: 20px;
    height: 20px;
    flex: none;
  }
</style>
</head>
<body>
<main class="stage">

  <section class="card card-front" aria-label="Card front">
    <div class="front-name"><span class="mark-square"></span>TMW Home Crafting</div>
  </section>

  <section class="card card-back" aria-label="Card back">
    <div class="brand-name"><span class="mark-square"></span>TMW Home Crafting</div>

    <div class="person">
      <h1 class="person-name">Liam Harper</h1>
      <p class="person-title">General Manager</p>
    </div>

    <div class="divider"></div>

    <ul class="contacts">
      <li class="contact">
        <svg class="icon" viewBox="0 0 20 20" aria-hidden="true">
          <circle cx="10" cy="10" r="10" fill="var(--green)"/>
          <path d="M6 5.5c.6-.5 1.3-.4 1.7.2l1 1.5c.3.5.2 1-.2 1.4l-.6.5c.6 1.2 1.4 2 2.6 2.6l.5-.6c.4-.4.9-.5 1.4-.2l1.5 1c.6.4.7 1.1.2 1.7l-.6.6c-.8.8-2.3.6-4.2-.8-1.6-1.2-2.7-2.6-3.3-4.1-.5-1.3-.4-2.4.2-3z" fill="#fff"/>
        </svg>
        0400 123 456
      </li>
      <li class="contact">
        <svg class="icon" viewBox="0 0 20 20" aria-hidden="true">
          <circle cx="10" cy="10" r="10" fill="var(--green)"/>
          <rect x="5" y="6.5" width="10" height="7" rx="1" fill="#fff"/>
          <path d="M5.5 7l4.5 3.5L14.5 7" fill="none" stroke="var(--green)" stroke-width="1"/>
        </svg>
        info@tmwhomecrafting.com.au
      </li>
      <li class="contact">
        <svg class="icon" viewBox="0 0 20 20" aria-hidden="true">
          <circle cx="10" cy="10" r="10" fill="var(--green)"/>
          <circle cx="10" cy="10" r="5" fill="none" stroke="#fff" stroke-width="1.2"/>
          <ellipse cx="10" cy="10" rx="2.2" ry="5" fill="none" stroke="#fff" stroke-width="1"/>
          <line x1="5" y1="10" x2="15" y2="10" stroke="#fff" stroke-width="1"/>
        </svg>
        www.tmwhomecrafting.com.au
      </li>
    </ul>

    <div class="address">
      <svg class="icon" viewBox="0 0 20 20" aria-hidden="true">
        <circle cx="10" cy="10" r="10" fill="var(--green)"/>
        <path d="M10 4.5a3.6 3.6 0 0 0-3.6 3.6c0 2.7 3.6 7 3.6 7s3.6-4.3 3.6-7A3.6 3.6 0 0 0 10 4.5z" fill="#fff"/>
        <circle cx="10" cy="8.1" r="1.3" fill="var(--green)"/>
      </svg>
      Kellbrook, Tasmania, Australia
    </div>
  </section>

</main>
</body>
</html>
```